Professional & attention grabbing.

A business card design, front and back. I already have a logo I will attach, but I am open to something new as well.
Things to include:
Name:
Title:
Phone:
Email:
Wanting something that is professional but attention grabbing.
Also we do a lot of work using drones on natural gas pipelines (leading the future)if you want to include any of that. I'm open to ideas.
Target Market(s)
Natural gas transmission industry / greenhouse gas mitigation industry
Industry/Entity Type
Business
Colors
Designer to choose colors to be used in the design.
Look and feel
Each slider illustrates characteristics of the customer's brand and the style your logo design should communicate.

```html
<!DOCTYPE html>
<html lang="en">
<head>
<meta charset="utf-8">
<title>Kestrel Inspections — Business Card</title>
<link rel="stylesheet" href="https://fonts.googleapis.com/css2?family=Montserrat:wght@400;600;700;800&display=swap">
<style>
  :root {
    --backdrop: #a4a5a7;
    --ink: #111111;
    --charcoal: #3a3a3b;
    --charcoal-deep: #2e2e2f;
    --steel-light: #b9bcc1;
    --steel-mid: #7d8189;
    --steel-dark: #3d4047;
    --amber: #f0b12c;
    --amber-deep: #e48f22;
    --amber-light: #f5cf4e;
    --paper: #ffffff;
    --paper-cool: #eef1f7;
    --brand-red: #c8161d;
    --name-grey: #444549;
  }
  html, body {
    margin: 0;
    padding: 0;
    width: 1200px;
    height: 1200px;
    overflow: hidden;
    background: var(--backdrop);
    font-family: "Montserrat", sans-serif;
  }
  .canvas {
    position: relative;
    width: 1200px;
    height: 1200px;
  }
  .side-label {
    position: absolute;
    left: 81px;
    margin: 0;
    font-family: "Montserrat", sans-serif;
    font-weight: 800;
    font-size: 26px;
    letter-spacing: 6px;
    color: var(--ink);
    line-height: 1;
  }
  .side-label--front { top: 278px; }
  .side-label--back { top: 802px; }
  .card {
    position: absolute;
    display: block;
    box-shadow: 0 18px 30px rgba(0, 0, 0, 0.12);
  }
  .card--front { left: 276px; top: 124px; width: 680px; height: 408px; }
  .card--back { left: 274px; top: 616px; width: 692px; height: 416px; }
  .brand-name {
    font-family: "Montserrat", sans-serif;
    font-weight: 700;
    font-size: 28px;
    fill: var(--charcoal);
  }
  .holder-name {
    font-family: "Montserrat", sans-serif;
    font-size: 25px;
    fill: var(--name-grey);
    letter-spacing: 0.5px;
  }
  .holder-name .given { font-weight: 400; }
  .holder-name .family { font-weight: 700; }
  .holder-title {
    font-family: "Montserrat", sans-serif;
    font-weight: 700;
    font-size: 13px;
    fill: var(--brand-red);
    letter-spacing: 0.3px;
  }
  .contact-text {
    font-family: "Montserrat", sans-serif;
    font-weight: 400;
    font-size: 15px;
    fill: var(--paper);
  }
</style>
</head>
<body>
<main class="canvas">

  <p class="side-label side-label--front">FRONT</p>

  <svg class="card card--front" viewBox="0 0 680 408" aria-label="Business card front">
    <defs>
      <linearGradient id="steel-sheen" x1="0" y1="0" x2="1" y2="0">
        <stop offset="0" stop-color="var(--steel-dark)"/>
        <stop offset="0.3" stop-color="var(--steel-mid)"/>
        <stop offset="0.5" stop-color="var(--steel-light)"/>
        <stop offset="0.75" stop-color="var(--steel-mid)"/>
        <stop offset="1" stop-color="var(--steel-dark)"/>
      </linearGradient>
      <linearGradient id="steel-lower" x1="0" y1="0" x2="0" y2="1">
        <stop offset="0" stop-color="#2c2e33"/>
        <stop offset="0.4" stop-color="#5e626a"/>
        <stop offset="1" stop-color="#9a9da3"/>
      </linearGradient>
      <linearGradient id="amber-front" x1="0" y1="0" x2="1" y2="1">
        <stop offset="0" stop-color="var(--amber)"/>
        <stop offset="1" stop-color="var(--amber-deep)"/>
      </linearGradient>
      <linearGradient id="band-front" x1="0" y1="0" x2="0" y2="1">
        <stop offset="0" stop-color="var(--paper-cool)"/>
        <stop offset="1" stop-color="var(--paper)"/>
      </linearGradient>
    </defs>
    <rect class="card-base" width="680" height="408" fill="url(#steel-sheen)"/>
    <polygon class="lower-plate" points="46,203 579,296 504,408 0,408 0,240" fill="url(#steel-lower)" opacity="0.85"/>
    <polygon class="accent-corner" points="0,0 174,0 0,273" fill="url(#amber-front)"/>
    <line x1="178" y1="0" x2="4" y2="274" stroke="var(--paper)" stroke-width="2" opacity="0.8"/>
    <polygon class="brand-band" points="106,108 680,108 680,146 579,296 46,203" fill="url(#band-front)"/>
    <polygon class="accent-corner" points="680,146 680,408 504,408" fill="url(#amber-front)"/>
    <line x1="678" y1="140" x2="498" y2="408" stroke="var(--paper)" stroke-width="3"/>
    <g class="brand-lockup">
      <rect x="190" y="164" width="22" height="22" fill="var(--brand-red)"/>
      <text class="brand-name" x="222" y="186">Kestrel Inspections</text>
    </g>
  </svg>

  <p class="side-label side-label--back">BACK</p>

  <svg class="card card--back" viewBox="0 0 692 416" aria-label="Business card back">
    <defs>
      <linearGradient id="amber-back" x1="0" y1="0" x2="1" y2="1">
        <stop offset="0" stop-color="var(--amber-light)"/>
        <stop offset="1" stop-color="var(--amber-deep)"/>
      </linearGradient>
      <linearGradient id="contact-shade" x1="0" y1="0" x2="0" y2="1">
        <stop offset="0" stop-color="#2a2a2b"/>
        <stop offset="0.12" stop-color="var(--charcoal)"/>
        <stop offset="1" stop-color="var(--charcoal)"/>
      </linearGradient>
    </defs>
    <rect class="card-base" width="692" height="416" fill="var(--charcoal-deep)"/>
    <polygon points="258,0 536,0 520,51 228,51" fill="#363637"/>
    <polygon class="accent-corner" points="0,0 258,0 228,51 0,51" fill="url(#amber-back)"/>
    <polygon class="accent-corner" points="0,138 140,164 68,288 0,288" fill="url(#amber-back)"/>
    <polygon class="accent-corner" points="536,0 692,0 692,288 672,288 520,51" fill="url(#amber-back)"/>
    <polygon class="name-band" points="0,51 513,51 663,258 146,160 0,130" fill="var(--paper)"/>
    <rect class="contact-bar" x="0" y="288" width="692" height="128" fill="url(#contact-shade)"/>

    <text class="holder-name" x="347" y="117" text-anchor="middle"><tspan class="given">MARISA </tspan><tspan class="family">CALDEN</tspan></text>
    <text class="holder-title" x="347" y="138" text-anchor="middle">GRAPHIC DESIGNER</text>

    <text class="contact-text" x="96" y="335">info@kestrel.com</text>
    <g class="icon-mail">
      <rect x="262" y="320" width="31" height="22" rx="2" fill="var(--amber)"/>
      <polyline points="262,320 277.5,333 293,320" fill="none" stroke="#8a5a10" stroke-width="1.6"/>
      <polyline points="262,342 274,331 M281,331 293,342" fill="none" stroke="#8a5a10" stroke-width="1.2"/>
    </g>

    <text class="contact-text" x="377" y="335">008 412 739 2056</text>
    <g class="icon-phone">
      <rect x="527" y="308" width="22" height="40" rx="4" fill="var(--amber)"/>
      <rect x="530" y="313" width="16" height="26" fill="#8a5a10"/>
      <circle cx="538" cy="343.5" r="2" fill="#8a5a10"/>
    </g>
  </svg>

</main>
</body>
</html>
```